Web Design Concept for new social network

We need a fresh, vibrant, clean web design layout for a new social network that we are trying to put together.
The site itself will be stuffed with little jquery/css tricks to enable a better/better looking UI (this is where you come in).
Imagine you were re-imagining Rallyhub.. How would you have designed it? The new site, will have a lot of similar functions to RH, and then a few more.
I will need a great looking sign in page in addition to;
The main page will need to have the following elements;
- Profile header.
Profile picture and tabbed area for various pieces of meta data contact details, preferences etc
- A Post Wall (like the wall on RH, but its crossed with a chirply-esque global search/post). People can respond to not only the original message, but can reply to each individual reply.
Instead of LIKE, there will need to be a positive/negative/neutral style option (feel free to get creative with naming). The background of each post will reflect the average rating (pos/nuetral/neg) of the post itself.. so if 100 people click pos, 50 neutral and 1 negative, the bg will mainly be the positive colour).
The feed will include messages by default from many sources (rallyhub/chirply/work loop) there should be somewhere that these can be switched on and off...
Somewhere to post a message - again by default it will post to all networks, but should be able to switch off.
Images/Videos/Text can all be posted to the wall (if you can think of a better name than wall - please use that!)
- Notifications; rather than having them in a drop down menu like rh, i want them to be in a hidden div (one div for each type) that slides open to reveal the notifications.. The default will be that the divs are closed so if there is a new notification there will be a need for something to appear on the screen that the user can click. We will need 3 notification types.
- Calendar; collapsable
- Options for today/this week/month views etc
- Menu system to navigate to other screens.
This should be able to show available things like groups/pages/events (again feel free to rename).
The screens themselves should appear to be stacked (like stacked tiles).
- Search; there should be a search bar somewhere with various options being available.
- Modal popup. I will be using modal popups across the site so will want a consistant feel (should be able to display photos/videos etc)
I will upload some files over the next few days to support the above, but am really looking for your creativity here.
Sites I really like the style of:
- the NEW yardnook (check it out.. its awesome).
- quince
- chirply
I want a really clean interface, modern.. splashes of colour are fine (but only where it will enhance).
Updates
I have added a file to the uploads that gives an idea of how the notifications should be revealed.. Please do not read too much into any styling... i created the pdf just to show how i expect the notifications to be revealed, and that I expect there to be multiple notification types.
Although I deliberately didnt request adverts to be shown in the brief, i also didnt explicitly state that they shouldnt be! The site will NOT feature adverts so please do not show them on the design. Id much rather that the space be used to improve layout.
Target Market(s)
18 to 40 - again, think rallyhub/chirply/workloop
Industry/Entity Type
Events
Look and feel

```html
<!DOCTYPE html>
<html lang="en">
<head>
<meta charset="utf-8">
<title>Nookwire.com — Sign Up</title>
<link href="https://fonts.googleapis.com/css2?family=Arimo:ital,wght@0,400;0,700;1,400&display=swap" rel="stylesheet">
<style>
:root{
  --brand-red:#a30d12;
  --brand-red-dark:#6e0509;
  --title-red:#c0141b;
  --ink:#2b2b2b;
  --muted:#555;
  --field-text:#555;
  --field-border:#d6d6d6;
  --page-bg:#e8e8e8;
  --card-bg:#f5f5f5;
  --white:#ffffff;
  --logo-grey:#7a7a7a;
}
*{box-sizing:border-box;margin:0;padding:0}
html,body{width:1200px;height:769px;overflow:hidden}
body{position:relative;background:var(--page-bg);font-family:"Arimo",Arial,sans-serif;color:var(--ink)}
.top-rule{position:absolute;left:0;top:0;width:1200px;height:6px;background:var(--brand-red)}
.site-header{position:absolute;left:0;top:6px;width:1200px;height:88px;background:linear-gradient(#ffffff,#f1f1f1);border-bottom:1px solid #dcdcdc}
.brand{position:absolute;left:82px;top:24px;font-size:38px;font-weight:700;color:var(--logo-grey);letter-spacing:-1px}
.login-field,.field,.picker{position:absolute;background:var(--white);border:1px solid var(--field-border);border-radius:6px;color:var(--field-text);display:flex;align-items:center}
.login-field{height:25px;top:20px;font-size:12px;padding-left:12px;color:#666}
.login-field.email{left:662px;width:192px}
.login-field.password{left:863px;width:192px}
.login-button{position:absolute;left:1062px;top:20px;width:55px;height:25px;border-radius:4px;background:linear-gradient(#b3151b,var(--brand-red-dark));color:var(--white);font-size:12px;display:flex;align-items:center;justify-content:center}
.remember{position:absolute;left:666px;top:54px;font-size:12px;color:#777;display:flex;align-items:center;gap:8px}
.remember .box{width:11px;height:11px;border:1px solid #aaa;background:#eee}
.forgot{position:absolute;left:863px;top:54px;font-size:12px;color:#777}
.signup-card{position:absolute;left:341px;top:113px;width:519px;height:570px;background:var(--card-bg);border:3px solid var(--white);border-radius:18px;box-shadow:0 0 0 1px #dedede}
.form-icon{position:absolute;left:275px;top:109px;width:120px;height:106px;border-radius:8px;background:linear-gradient(135deg,#4a9ad0,#e8eef3 45%,#f3c64a);transform:rotate(-8deg)}
.signup-title{position:absolute;left:403px;top:155px;font-size:23px;color:var(--title-red)}
.signup-sub{position:absolute;left:403px;top:183px;font-size:18px;color:var(--ink)}
.field{left:398px;width:361px;height:34px;font-size:13px;padding-left:14px}
.picker{height:35px;font-size:13px;padding-left:12px}
.picker .arrow{position:absolute;right:8px;top:9px;width:17px;height:17px;border:1px solid #666;background:#eee;display:flex;align-items:center;justify-content:center}
.gender{left:398px;top:456px;width:166px;padding-left:23px}
.birthday-label{position:absolute;left:398px;top:514px;font-size:13px;color:var(--muted)}
.day{left:492px;top:505px;width:73px}
.month{left:575px;top:505px;width:87px}
.year{left:672px;top:505px;width:87px}
.signup-button{position:absolute;left:397px;top:562px;width:153px;height:41px;border-radius:10px;background:linear-gradient(#c01b22,var(--brand-red-dark));box-shadow:0 2px 3px rgba(0,0,0,.35);color:var(--white);font-size:17px;font-weight:700;display:flex;align-items:center;justify-content:center}
.legal{position:absolute;left:400px;top:615px;width:420px;font-size:11.5px;font-style:italic;line-height:16px;color:#333}
.legal a{color:var(--title-red);text-decoration:none}
.site-footer{position:absolute;left:0;top:711px;width:1200px;height:51px;background:var(--white);border-top:1px solid #dcdcdc;display:flex;align-items:center;justify-content:center;font-size:13.5px;color:#333}
.site-footer span.sep{margin:0 14px;color:#555}
.bottom-rule{position:absolute;left:0;top:762px;width:1200px;height:7px;background:var(--brand-red)}
</style>
</head>
<body>
<div class="top-rule"></div>
<header class="site-header">
  <div class="brand">Nookwire.com</div>
</header>
<div class="login-field email">Your email address</div>
<div class="login-field password">Password</div>
<div class="login-button">LOGIN</div>
<div class="remember"><span class="box"></span>Keep me logged in</div>
<div class="forgot">Forgotten your password?</div>

<main class="signup-card"></main>
<div class="form-icon" role="img" aria-label="Illustration of a profile form with a pencil"></div>
<h1 class="signup-title" style="font-weight:400">SIGN UP</h1>
<p class="signup-sub">It’s free for all</p>

<div class="field" style="top:214px">First Name</div>
<div class="field" style="top:262px">Surname</div>
<div class="field" style="top:310px">Your Email</div>
<div class="field" style="top:357px">Re-enter Email</div>
<div class="field" style="top:406px">New Password</div>

<div class="picker gender">Select Gender<span class="arrow"><svg width="9" height="6"><path d="M0 0h9L4.5 6z" fill="#222"/></svg></span></div>
<div class="birthday-label">(Your Birthday)</div>
<div class="picker day">Day<span class="arrow"><svg width="9" height="6"><path d="M0 0h9L4.5 6z" fill="#222"/></svg></span></div>
<div class="picker month">Month<span class="arrow"><svg width="9" height="6"><path d="M0 0h9L4.5 6z" fill="#222"/></svg></span></div>
<div class="picker year">Year<span class="arrow"><svg width="9" height="6"><path d="M0 0h9L4.5 6z" fill="#222"/></svg></span></div>

<div class="signup-button">SIGN UP NOW</div>
<p class="legal">By clicking Sign Up, you agree to our <a href="#">Terms</a> and that you have read our <a href="#">Data use policy,</a> including our Cookie Use.</p>

<footer class="site-footer">
  About<span class="sep">|</span>Help<span class="sep">|</span>Blog<span class="sep">|</span>Status<span class="sep">|</span>Jobs<span class="sep">|</span>Terms Privacy<span class="sep">|</span>Advertisers<span class="sep">|</span>Businesses Media<span class="sep">|</span>Developers<span class="sep">|</span>Resources<span class="sep">|</span>Directory
</footer>
<div class="bottom-rule"></div>
</body>
</html>
```